Birch Hauling Business Card Design Project

We need a new company business card. We provide professional timber harvesting (logging) and forest management services. I'm open to any creative design. Most company caps and shirts are navy blue and Light grey. Logo does not necessarily have to contain those colors. Logo containing picture of logging equipment, log truck, trees, or logs are acceptable. Be creative. Final logo should communicate our company's pride and professionalism in the East Texas Timber Industry.
Updates

Target Market(s)

Timber owners, sawmills, and forestry professionals

Industry/Entity Type

Business

Requirements
Must have
• Must have Contact Info.
Phone: 936-402-5917
address: PO Box 4830
New Waverly, Tx 77358
www.jmbirchhauling.example
jmbirchhauling@mailbox.example
Owner: Jared Marsh

Or design must leave room for this info.

```html
<!DOCTYPE html>
<html lang="en">
<head>
<meta charset="utf-8">
<title>Birch Hauling – Business Card</title>
<link rel="stylesheet" href="https://fonts.googleapis.com/css2?family=Exo+2:wght@400;600;700&display=swap">
<style>
  :root {
    --backdrop: #ecebe8;
    --brand-red: #e8282f;
    --brand-red-light: #f0474c;
    --paper: #ffffff;
    --paper-shade: #e4e4e6;
    --ink: #3a3a3c;
    --on-red: #ffffff;
  }
  * { box-sizing: border-box; margin: 0; padding: 0; }
  html, body { width: 1200px; height: 828px; overflow: hidden; }
  body {
    background: var(--backdrop);
    font-family: "Exo 2", Arial, sans-serif;
    display: flex;
    align-items: center;
    justify-content: center;
    gap: 50px;
  }
  .card {
    position: relative;
    width: 525px;
    height: 300px;
    overflow: hidden;
    box-shadow: 0 6px 18px rgba(0,0,0,.18);
  }
  .card-art { position: absolute; inset: 0; }

  /* back */
  .card--back { background: linear-gradient(180deg, var(--paper) 40%, var(--paper-shade)); }
  .back-website {
    position: absolute;
    left: 0; right: 0; top: 222px;
    text-align: center;
    font-size: 17px;
    letter-spacing: 5px;
    color: var(--ink);
  }

  /* front */
  .card--front { background: linear-gradient(160deg, var(--brand-red-light), var(--brand-red)); }
  .brand {
    position: absolute;
    left: 34px; top: 192px;
    display: flex;
    align-items: center;
    gap: 12px;
  }
  .brand-mark { width: 24px; height: 24px; background: var(--brand-red); flex: none; }
  .brand-name {
    font-weight: 700;
    font-size: 21px;
    line-height: 1.1;
    text-transform: uppercase;
    color: var(--ink);
  }
  .holder {
    position: absolute;
    right: 26px; top: 24px;
    text-align: right;
    color: var(--on-red);
  }
  .holder-name { font-size: 17px; font-weight: 600; letter-spacing: 1.5px; text-transform: uppercase; }
  .holder-role { font-size: 11px; letter-spacing: .5px; }
  .contact-list {
    position: absolute;
    right: 26px; top: 90px;
    list-style: none;
    color: var(--on-red);
    font-size: 10.5px;
    text-align: right;
    white-space: nowrap;
  }
  .contact-list li {
    display: flex;
    justify-content: flex-end;
    align-items: center;
    gap: 8px;
    line-height: 19px;
  }
  .contact-list .address { line-height: 14px; margin-bottom: 10px; align-items: flex-start; }
  .contact-icon { width: 11px; height: 11px; flex: none; }
</style>
</head>
<body>

  <section class="card card--back" aria-label="Card back">
    <svg class="card-art" viewBox="0 0 525 300" aria-hidden="true">
      <defs>
        <linearGradient id="backRed" x1="0" y1="0" x2="0" y2="1">
          <stop offset="0" stop-color="#ee3a40"/>
          <stop offset="1" stop-color="#e2232b"/>
        </linearGradient>
        <linearGradient id="backSilver" x1="0" y1="0" x2="1" y2="0">
          <stop offset="0" stop-color="#d9dbde"/>
          <stop offset=".5" stop-color="#9fa2a7"/>
          <stop offset="1" stop-color="#f2f3f4"/>
        </linearGradient>
      </defs>
      <path d="M0,186 C200,204 420,150 525,18 V40 C420,170 200,218 0,198 Z" fill="url(#backSilver)"/>
      <path d="M0,0 H525 V14 C420,144 200,194 0,176 Z" fill="url(#backRed)"/>
    </svg>
    <p class="back-website">www.jmbirchhauling.example</p>
  </section>

  <section class="card card--front" aria-label="Card front">
    <svg class="card-art" viewBox="0 0 525 300" aria-hidden="true">
      <defs>
        <linearGradient id="frontSilver" x1="0" y1="0" x2="1" y2="1">
          <stop offset="0" stop-color="#eef0f1"/>
          <stop offset=".5" stop-color="#a4a7ab"/>
          <stop offset="1" stop-color="#dfe1e3"/>
        </linearGradient>
        <linearGradient id="frontPaper" x1="0" y1="0" x2="0" y2="1">
          <stop offset="0" stop-color="#ffffff"/>
          <stop offset="1" stop-color="#e6e6e8"/>
        </linearGradient>
      </defs>
      <path d="M0,92 C170,50 320,120 350,300 H0 Z" fill="url(#frontSilver)"/>
      <path d="M0,104 C160,64 305,130 335,300 H0 Z" fill="url(#frontPaper)"/>
    </svg>

    <div class="brand">
      <span class="brand-mark"></span>
      <p class="brand-name">Jared Marsh<br>Birch Hauling</p>
    </div>

    <div class="holder">
      <p class="holder-name">Jared Marsh</p>
      <p class="holder-role">Owner</p>
    </div>

    <ul class="contact-list">
      <li class="address"><span>PO Box 4830<br>New Waverly, TX 77358</span>
        <svg class="contact-icon" viewBox="0 0 12 12"><path d="M6 0.5a4 4 0 0 1 4 4c0 3-4 7-4 7s-4-4-4-7a4 4 0 0 1 4-4z" fill="#fff"/><circle cx="6" cy="4.5" r="1.4" fill="#e8282f"/></svg></li>
      <li><span>936-402-5917</span>
        <svg class="contact-icon" viewBox="0 0 12 12"><path d="M2 1h2.5l1 3-1.5 1a7 7 0 0 0 3 3l1-1.5 3 1V11A10 10 0 0 1 1 2z" fill="#fff"/></svg></li>
      <li><span>936-402-5918</span>
        <svg class="contact-icon" viewBox="0 0 12 12"><rect x="3" y="0.5" width="6" height="11" rx="1" fill="none" stroke="#fff"/><circle cx="6" cy="9.5" r=".8" fill="#fff"/></svg></li>
      <li><span>936-402-5919</span>
        <svg class="contact-icon" viewBox="0 0 12 12"><rect x="1" y="4" width="10" height="6" fill="#fff"/><rect x="3" y="1" width="6" height="3" fill="none" stroke="#fff"/></svg></li>
      <li><span>jmbirchhauling@mailbox.example</span>
        <svg class="contact-icon" viewBox="0 0 12 12"><rect x="0.5" y="2.5" width="11" height="7" fill="#fff"/><path d="M0.5 2.5 6 7l5.5-4.5" fill="none" stroke="#e8282f"/></svg></li>
      <li><span>www.jmbirchhauling.example</span>
        <svg class="contact-icon" viewBox="0 0 12 12"><circle cx="6" cy="6" r="5" fill="none" stroke="#fff"/><ellipse cx="6" cy="6" rx="2" ry="5" fill="none" stroke="#fff"/><path d="M1 6h10" stroke="#fff"/></svg></li>
    </ul>
  </section>

</body>
</html>
```